Refresh Brightpath Coursecraft

Need a new design for e-learning development and web app development site: http://brightpathcoursecraft.example. Need pages for everything on menu bar plus a training services and a web app development services pages and a better page for samples http://brightpathcoursecraft.example/samples5/.

***Must be programmed in html 5. NO CMS. No WP. No Plume. Straight html/css.

Target Market(s)

government

Industry/Entity Type

Government

Coding

Coded - Design and coding required

Number of Pages Required

1 page

Requirements
Must have
• Must be coded in html5/css. No CMS.
• Divided so you can easily see that we offer 3 separate services:
• Live Training - E-Learning Development - Web App Development
• A way to display logos of all our clients like on bottom of this page: https://www.quorvatests.example (this is also our website so you can copy all these logos)
• List both our Denver location which is already on our website plus our office in Velmoro Plaza. Street 62 Sur, 14-87. Medellín, Antioquia.
• A page like this for our web app dev services https://www.tekvanu.example/product-development
Should not have
• CMS

```html
<!DOCTYPE html>
<html lang="en">
<head>
<meta charset="utf-8">
<title>Brightpath Coursecraft</title>
<link href="https://fonts.googleapis.com/css2?family=Poppins:wght@400;500;600&family=Source+Sans+3:wght@600;700&display=swap" rel="stylesheet">
<style>
:root{
  --blue:#1b7fc2;
  --orange:#f4a11f;
  --ink:#161616;
  --body:#3a3a3a;
  --grey:#f3f3f3;
  --black:#000;
  --white:#fff;
}
*{box-sizing:border-box;margin:0;padding:0}
html,body{width:1200px;height:3782px;overflow:hidden}
body{position:relative;background:var(--white);font-family:'Poppins',sans-serif;color:var(--body)}
.abs{position:absolute}
/* header */
.site-header{left:0;top:0;width:1200px;height:100px;background:var(--white)}
.brand{left:96px;top:18px;display:flex;align-items:center;gap:14px}
.brand-dot{width:58px;height:58px;border-radius:50%;background:var(--blue)}
.brand-name{font-family:'Poppins',sans-serif;font-weight:600;font-size:22px;line-height:1.05;color:var(--orange)}
.nav{left:428px;top:38px;display:flex;gap:26px;font-family:'Poppins',sans-serif;font-weight:500;font-size:16px;color:var(--ink)}
.call{left:924px;top:26px;display:flex;align-items:center;gap:12px}
.call-icon{width:50px;height:50px;border-radius:50%;background:var(--blue);display:flex;align-items:center;justify-content:center}
.call-text{font-size:15px;line-height:1.2;color:var(--ink);font-weight:500}
.call-text span{display:block;color:var(--orange)}
/* hero */
.hero{left:0;top:100px;width:1200px;height:540px}
.hero-title{left:0;top:192px;width:1200px;text-align:center;font-family:'Source Sans 3',sans-serif;font-weight:700;font-size:48px;line-height:1.3;color:var(--white)}
.arrow-btn{width:48px;height:48px;border-radius:50%;background:var(--white);box-shadow:0 2px 6px rgba(0,0,0,.25);display:flex;align-items:center;justify-content:center}
/* welcome */
.welcome-mark{left:555px;top:760px;width:90px;height:90px;border-radius:50%;background:var(--orange)}
.welcome-title{left:0;top:885px;width:1200px;text-align:center;font-family:'Source Sans 3',sans-serif;font-weight:600;font-size:46px;line-height:1.26;color:var(--ink)}
.lead{left:210px;top:1038px;width:780px;text-align:center;font-size:17px;line-height:1.95;color:var(--body)}
/* services */
.illus{border-radius:18px}
.svc-title{font-family:'Source Sans 3',sans-serif;font-weight:600;font-size:46px;color:var(--ink);white-space:nowrap}
.svc-title em{font-style:normal;color:var(--blue)}
.svc-text{width:520px;font-size:17px;line-height:1.98;color:var(--body)}
.btn{width:194px;height:60px;border:2px solid var(--blue);border-radius:30px;display:flex;align-items:center;justify-content:center;font-weight:500;font-size:17px;color:var(--blue)}
/* clients */
.clients{left:0;top:2626px;width:1200px;height:700px;background:var(--grey)}
.clients-title{left:0;top:2722px;width:1200px;text-align:center;font-family:'Source Sans 3',sans-serif;font-weight:600;font-size:46px;color:var(--ink)}
.clients-title em{font-style:normal;color:var(--blue)}
.client{width:170px;height:113px;background:var(--white);display:flex;flex-direction:column;align-items:center;justify-content:center;gap:8px;font-size:14px;font-weight:500;color:var(--blue);text-align:center}
.client i{display:block;width:34px;height:34px;border-radius:50%;background:var(--blue)}
/* footer */
.footer-bg{left:0;top:3210px;width:1200px;height:572px}
.f-head{font-weight:600;font-size:21px;color:var(--white)}
.f-text{font-size:16px;line-height:2;color:var(--white)}
.contact-row{left:96px;display:flex;gap:30px;align-items:flex-start}
.contact-row svg{flex:none}
.links{left:950px;top:3405px;list-style:none;font-size:16px;line-height:2;color:var(--white)}
.news-field{left:493px;top:3538px;width:330px;height:46px;display:flex}
.news-field input{flex:1;border:0;padding:0 12px;font-family:'Poppins',sans-serif;font-size:13px;color:#666}
.news-field button{width:70px;border:0;background:var(--blue);display:flex;align-items:center;justify-content:center}
.socials{left:500px;top:3617px;display:flex;gap:22px}
.socials span{width:32px;height:32px;background:var(--white);border-radius:3px}
.copyright{left:0;top:3738px;width:1200px;text-align:center;font-size:17px;color:var(--white)}
</style>
</head>
<body>

<header class="site-header abs">
  <div class="brand abs"><div class="brand-dot"></div><div class="brand-name">BRIGHTPATH<br>COURSECRAFT</div></div>
  <nav class="nav abs"><span>HOME</span><span>PORTFOLIO</span><span>TEAM &amp; EXPERIENCE</span><span>CONTACTS</span></nav>
  <div class="call abs">
    <div class="call-icon"><svg width="24" height="24" viewBox="0 0 24 24"><path d="M6.6 10.8a15 15 0 0 0 6.6 6.6l2.2-2.2c.3-.3.7-.4 1-.2 1.1.4 2.3.6 3.6.6.6 0 1 .4 1 1V20c0 .6-.4 1-1 1A17 17 0 0 1 3 4c0-.6.4-1 1-1h3.5c.6 0 1 .4 1 1 0 1.3.2 2.5.6 3.6.1.3 0 .7-.2 1z" fill="#fff"/></svg></div>
    <div class="call-text">CALL US<span>555-214-7730</span></div>
  </div>
</header>

<svg class="hero abs" viewBox="0 0 1200 540" role="img" aria-label="Photo of a student studying at a laptop showing an e-learning screen">
  <defs><linearGradient id="heroGrad" x1="0" y1="0" x2="1" y2="1"><stop offset="0" stop-color="#3b3530"/><stop offset=".5" stop-color="#6a5c4f"/><stop offset="1" stop-color="#26221f"/></linearGradient></defs>
  <path d="M0 0H1200V455Q600 640 0 455Z" fill="url(#heroGrad)"/>
  <path d="M0 462Q600 650 1200 462" fill="none" stroke="var(--blue)" stroke-width="10"/>
</svg>
<h1 class="hero-title abs">We create engaging training<br>that exceed expectations.</h1>
<div class="arrow-btn abs" style="left:31px;top:298px"><svg width="14" height="14" viewBox="0 0 14 14"><path d="M9 2L4 7l5 5" stroke="#222" stroke-width="2" fill="none"/></svg></div>
<div class="arrow-btn abs" style="left:1121px;top:298px"><svg width="14" height="14" viewBox="0 0 14 14"><path d="M5 2l5 5-5 5" stroke="#222" stroke-width="2" fill="none"/></svg></div>

<div class="welcome-mark abs"></div>
<h2 class="welcome-title abs">Welcome to<br>Brightpath Coursecraft</h2>
<p class="lead abs">Lorem Ipsum is simply dummy text of the printing and typesetting industry. Lorem Ipsum has been the industry's standard dummy text ever since the 1500s, when an unknown printer took a galley of type and scrambled it to make a type specimen book. It has survived not only five centuries, but also the leap into electronic typesetting, remaining essentially unchanged.</p>

<!-- Live Training -->
<div class="illus abs" role="img" aria-label="Illustration of a trainer on a video screen teaching a group seated at a table" style="left:100px;top:1285px;width:380px;height:365px;background:linear-gradient(160deg,#dcebf7,#f7e2cf)"></div>
<h2 class="svc-title abs" style="left:585px;top:1305px"><em>Live</em> Training</h2>
<p class="svc-text abs" style="left:585px;top:1380px">Lorem Ipsum is simply dummy text of the printing and typesetting industry. Lorem Ipsum has been the industry's standard dummy text ever since the 1500s, when an unknown printer took a galley of type and scrambled</p>
<div class="btn abs" style="left:585px;top:1584px">READ MORE</div>

<!-- E-Learning -->
<h2 class="svc-title abs" style="left:96px;top:1755px"><em>E-Learning</em> Development</h2>
<p class="svc-text abs" style="left:96px;top:1830px">Lorem Ipsum is simply dummy text of the printing and typesetting industry. Lorem Ipsum has been the industry's standard dummy text ever since the 1500s, when an unknown printer took a galley of type and scrambled</p>
<div class="btn abs" style="left:96px;top:2036px">READ MORE</div>
<div class="illus abs" role="img" aria-label="Illustration of learners around a large open book, a light bulb and a laptop" style="left:680px;top:1740px;width:430px;height:290px;background:linear-gradient(160deg,#fdf1d2,#d7e7f5)"></div>

<!-- Web App -->
<div class="illus abs" role="img" aria-label="Illustration of workers and cranes assembling app tiles on a smartphone" style="left:100px;top:2190px;width:405px;height:330px;background:linear-gradient(160deg,#d9eef4,#e9e1f3)"></div>
<h2 class="svc-title abs" style="left:597px;top:2180px"><em>Web App</em> Development</h2>
<p class="svc-text abs" style="left:597px;top:2255px">Lorem Ipsum is simply dummy text of the printing and typesetting industry. Lorem Ipsum has been the industry's standard dummy text ever since the 1500s, when an unknown printer took a galley of type and scrambled</p>
<div class="btn abs" style="left:597px;top:2470px">READ MORE</div>

<!-- Clients -->
<div class="clients abs"></div>
<h2 class="clients-title abs">Our <em>Clients</em></h2>
<div class="client abs" style="left:113px;top:2815px"><i></i>Skyward Corps</div>
<div class="client abs" style="left:314px;top:2815px"><i></i>Hollis Ridge U</div>
<div class="client abs" style="left:515px;top:2815px"><i></i>Amberline State</div>
<div class="client abs" style="left:716px;top:2815px"><i></i>Norvale College</div>
<div class="client abs" style="left:916px;top:2815px"><i></i>Sunmere Labs</div>
<div class="client abs" style="left:113px;top:2968px"><i></i>Westhaven U</div>
<div class="client abs" style="left:314px;top:2968px"><i></i>Crestmark Academy</div>
<div class="client abs" style="left:515px;top:2968px"><i></i>Ridgefire Service</div>
<div class="client abs" style="left:716px;top:2968px"><i></i>Silverton Board</div>
<div class="client abs" style="left:916px;top:2968px"><i></i>Lakemont County</div>
<div class="arrow-btn abs" style="left:31px;top:2918px"><svg width="14" height="14" viewBox="0 0 14 14"><path d="M9 2L4 7l5 5" stroke="#222" stroke-width="2" fill="none"/></svg></div>
<div class="arrow-btn abs" style="left:1121px;top:2918px"><svg width="14" height="14" viewBox="0 0 14 14"><path d="M5 2l5 5-5 5" stroke="#222" stroke-width="2" fill="none"/></svg></div>

<!-- Footer -->
<svg class="footer-bg abs" viewBox="0 0 1200 572">
  <path d="M0 130Q600 -60 1200 130V572H0Z" fill="var(--black)"/>
  <path d="M0 124Q600 -66 1200 124" fill="none" stroke="var(--blue)" stroke-width="10"/>
</svg>

<h3 class="f-head abs" style="left:96px;top:3358px">Contact Us</h3>
<div class="contact-row abs" style="top:3418px">
  <svg width="30" height="40" viewBox="0 0 24 32"><path d="M12 0a11 11 0 0 0-11 11c0 8 11 21 11 21s11-13 11-21A11 11 0 0 0 12 0zm0 15a4 4 0 1 1 0-8 4 4 0 0 1 0 8z" fill="#fff"/></svg>
  <p class="f-text">8830 E Larkspur Avenue, Suite<br>2-115 Aurora, CO. 80012</p>
</div>
<div class="contact-row abs" style="top:3500px">
  <svg width="30" height="40" viewBox="0 0 24 32"><path d="M12 0a11 11 0 0 0-11 11c0 8 11 21 11 21s11-13 11-21A11 11 0 0 0 12 0zm0 15a4 4 0 1 1 0-8 4 4 0 0 1 0 8z" fill="#fff"/></svg>
  <p class="f-text">Velmoro Plaza. Street 62<br>Sur, 14-87. Medellín,<br>Antioquia.</p>
</div>
<div class="contact-row abs" style="top:3617px">
  <svg width="40" height="36" viewBox="0 0 40 36"><path d="M6 20V16a14 14 0 0 1 28 0v4" stroke="#fff" stroke-width="3" fill="none"/><rect x="3" y="19" width="8" height="13" rx="3" fill="#fff"/><rect x="29" y="19" width="8" height="13" rx="3" fill="#fff"/></svg>
  <p class="f-text" style="margin-left:-10px">+1 555 214 7730</p>
</div>
<div class="contact-row abs" style="top:3682px">
  <svg width="44" height="32" viewBox="0 0 44 32"><rect x="1" y="1" width="42" height="30" fill="#fff"/><path d="M2 2l20 16L42 2M2 30l15-14M42 30L27 16" stroke="#000" stroke-width="2" fill="none"/></svg>
  <p class="f-text" style="margin-left:-14px">support@brightpathcoursecraft.example</p>
</div>

<h3 class="f-head abs" style="left:493px;top:3358px">Newsletter</h3>
<p class="f-text abs" style="left:493px;top:3410px;width:340px;line-height:2">But I must explain to you how all this mistaken idea of denouncing pleasure and praising.</p>
<div class="news-field abs"><input type="email" placeholder="Enter your email address"><button aria-label="Subscribe"><svg width="18" height="14" viewBox="0 0 18 14"><path d="M0 7h15M10 2l5 5-5 5" stroke="#fff" stroke-width="2" fill="none"/></svg></button></div>
<div class="socials abs" aria-label="Social links"><span></span><span></span><span></span><span></span></div>

<h3 class="f-head abs" style="left:943px;top:3350px">Quick Links</h3>
<ul class="links abs"><li>HOME</li><li>PORTFOLIO</li><li>TEAM &amp; EXPERIENCE</li><li>CONTACTS</li></ul>

<p class="copyright abs">© 2019 Copyrights | Al Rights Reserved</p>

</body>
</html>
```